Ductless Mini Split Business Website

Copper Fern Services is looking to design an eye catching educational website about installing Ductless mini splits.

Similar to this company.
https://www.halvikstream.com/

Coding

Coded - Design and coding required

```html
<!DOCTYPE html>
<html lang="en">
<head>
<meta charset="utf-8">
<title>Copper Fern Services – Ductless Experts</title>
<link href="https://fonts.googleapis.com/css2?family=Alfa+Slab+One&family=Open+Sans:wght@300;400;600;700&display=swap" rel="stylesheet">
<style>
:root{
  --gold:#e6a01d;
  --gold-deep:#d8961a;
  --slate:#34434f;
  --ink:#2b2b2b;
  --mist:#eceff4;
  --snow:#dde4ec;
  --white:#ffffff;
  --muted:#6b7480;
}
*{box-sizing:border-box;margin:0;padding:0}
html,body{width:1200px;height:3661px;overflow:hidden}
body{position:relative;background:var(--mist);font-family:"Open Sans",sans-serif;color:var(--ink)}
.abs{position:absolute}
.slab{font-family:"Alfa Slab One",serif;font-weight:400}
/* header */
.site-header{left:0;top:0;width:1200px;height:131px;background:var(--white);z-index:5}
.brand{left:109px;top:7px;width:239px;height:114px;display:flex;flex-direction:column;align-items:center;justify-content:center;gap:6px}
.brand-row{display:flex;align-items:center;gap:10px}
.brand-dot{width:30px;height:30px;border-radius:50%;background:var(--gold)}
.brand-name{font-weight:700;font-size:21px;color:var(--ink);line-height:1.05}
.brand-tag{font-weight:700;font-size:20px;color:var(--ink);letter-spacing:.5px}
.main-nav a{position:absolute;top:56px;font-size:13.5px;color:#444;text-decoration:none;white-space:nowrap}
.main-nav a.active{color:var(--gold)}
.main-nav a.active::after{content:"";position:absolute;left:0;right:0;top:26px;height:2px;background:var(--gold)}
/* hero */
.hero{left:0;top:131px;width:1200px;height:736px;background:linear-gradient(160deg,#6d7883 0%,#56636f 45%,#3c4854 100%);clip-path:polygon(0 0,100% 0,100% 615px,0 100%);z-index:2}
.hero-title{left:0;top:318px;width:1200px;text-align:center;font-size:62px;color:var(--white);z-index:3}
.hero-sub{left:0;top:393px;width:1200px;text-align:center;font-size:27px;font-weight:300;color:var(--white);z-index:3}
.btn{display:flex;align-items:center;justify-content:center;border-radius:30px;background:var(--gold);color:var(--white);font-weight:700;font-size:15px;letter-spacing:1px;text-transform:uppercase;box-shadow:0 0 0 3px var(--mist),0 0 0 5px var(--gold)}
.hero-btn{left:473px;top:463px;width:254px;height:52px;z-index:3;box-shadow:0 0 0 3px rgba(255,255,255,.0),0 0 0 4px var(--gold)}
.dots{left:568px;top:759px;display:flex;gap:9px;z-index:3}
.dots span{width:8px;height:8px;border-radius:50%;background:#c9cdd2}
.dots span.on{background:var(--gold)}
/* about */
.snow-band{left:0;top:746px;width:1200px;height:772px;background:linear-gradient(180deg,#e8edf3,#d3dbe5);clip-path:polygon(0 0,100% 0,100% 654px,0 100%);z-index:1}
.about-panel{left:111px;top:852px;width:601px;height:611px;background:var(--slate);z-index:4;color:var(--white)}
.about-panel h2{position:absolute;left:46px;top:56px;font-size:37px;line-height:37px}
.rule{height:3px;background:var(--gold);width:55px}
.about-panel .rule{position:absolute;left:47px;top:142px}
.about-lead{position:absolute;left:46px;top:160px;width:400px;font-size:21px;line-height:29px}
.about-copy{position:absolute;left:46px;top:234px;width:395px;font-size:12.6px;line-height:23.2px;color:#e6ebef}
.about-copy p+p{margin-top:5px}
.about-frame{left:597px;top:968px;width:491px;height:378px;background:#5b6670;z-index:5}
.about-photo{left:604px;top:977px;width:484px;height:362px;background:linear-gradient(120deg,#eef3f6 0%,#b7cad5 55%,#7f9aac 100%);z-index:6}
/* services */
.help-title{left:0;top:1588px;width:1200px;text-align:center;font-size:37px;color:var(--gold)}
.help-rule{left:561px;top:1645px;width:78px;height:3px;background:var(--gold)}
.svc-card{width:305px;height:260px;border:2px solid var(--gold);background:#d9dee3;overflow:hidden}
.svc-photo{position:absolute;inset:0;background:linear-gradient(160deg,#f2f4f6,#b9c1c9)}
.svc-label{position:absolute;left:0;right:0;bottom:0;height:82px;background:var(--gold);clip-path:polygon(0 14px,100% 0,100% 100%,0 100%);display:flex;align-items:center;justify-content:center;text-align:center;padding-top:18px;color:var(--white);font-weight:700;font-size:15px;letter-spacing:1.2px;line-height:19px;text-transform:uppercase}
.more-btn{left:473px;top:2356px;width:254px;height:54px}
/* contact */
.contact-bg{left:0;top:2488px;width:1200px;height:799px;background:linear-gradient(180deg,#5b6067 0%,#484d54 60%,#3d4147 100%);clip-path:polygon(0 43px,100% 0,100% 100%,0 100%)}
.contact-title{left:111px;top:2628px;width:408px;text-align:center;font-size:40px;color:var(--white)}
.contact-rule{left:276px;top:2681px;width:78px;height:3px;background:var(--white)}
.contact-sub{left:111px;top:2699px;width:408px;text-align:center;font-size:20px;color:var(--white)}
.field{background:var(--white);height:41px;font-size:13.5px;color:#777;padding:12px 19px}
.field.msg{height:84px}
.send-btn{left:189px;top:3050px;width:253px;height:55px;box-shadow:0 0 0 3px rgba(0,0,0,0),0 0 0 4px var(--gold)}
.why-panel{left:587px;top:2490px;width:502px;height:581px;background:var(--slate);color:var(--white);z-index:3}
.why-panel h2{position:absolute;left:50px;top:34px;font-size:38px;line-height:36px}
.why-item{position:absolute;left:50px;width:420px}
.why-icon{position:absolute;left:0;width:58px;height:58px;border-radius:50%;background:var(--gold);box-shadow:0 0 0 3px var(--slate),0 0 0 4px var(--gold)}
.why-icon svg{position:absolute;left:15px;top:15px}
.why-text{position:absolute;left:72px;width:345px}
.why-text h3{font-size:17.5px;font-weight:400;line-height:23px}
.why-text p{font-size:11.3px;line-height:20px;color:#dfe4e8;margin-top:3px}
/* footer */
.footer{left:0;top:3114px;width:1200px;height:547px;background:linear-gradient(180deg,#e2a420,#d8981b);clip-path:polygon(0 173px,100% 0,100% 100%,0 100%)}
.f-brand{left:112px;top:3340px;width:260px}
.f-brand .brand-name{color:#1f1f1f;font-size:24px}
.f-brand .brand-dot{background:#1f1f1f;width:32px;height:32px}
.f-tag{left:118px;top:3422px;font-size:24px;color:#1f1f1f;letter-spacing:1px}
.f-head{font-size:21px;color:var(--white);letter-spacing:.5px}
.social{display:flex;gap:8px}
.social span{width:42px;height:42px;border-radius:50%;background:var(--white)}
.f-line{font-size:15px;color:var(--white);display:flex;align-items:flex-start;gap:8px;line-height:28px}
.f-links a{position:absolute;left:928px;font-size:15.5px;color:var(--white);text-decoration:none}
.f-rule{left:112px;top:3599px;width:976px;height:1px;background:rgba(255,255,255,.5)}
.copyright{left:0;top:3618px;width:1200px;text-align:center;font-size:14px;color:var(--white)}
</style>
</head>
<body>

<header class="abs site-header">
  <div class="abs brand">
    <div class="brand-row"><span class="brand-dot"></span><span class="brand-name">Copper Fern Services</span></div>
    <div class="brand-tag">DUCTLESS EXPERTS</div>
  </div>
  <nav class="main-nav">
    <a class="active" style="left:431px">Home</a>
    <a style="left:508px">About Us</a>
    <a style="left:604px">Our Services</a>
    <a style="left:722px">Ductless Experts</a>
    <a style="left:864px">Blog</a>
    <a style="left:932px">Reviews</a>
    <a style="left:1021px">Contact Us</a>
  </nav>
</header>

<section>
  <div class="abs snow-band" role="img" aria-label="Soft frosty background with drifting snowflakes"></div>
  <div class="abs hero" role="img" aria-label="Woman relaxing on a sofa using a remote under a wall-mounted ductless unit"></div>
  <h1 class="abs slab hero-title">Ductless Experts It Better</h1>
  <p class="abs hero-sub">Molestias Excepturi Sint Occaecati Cupiditate Provident</p>
  <div class="abs btn hero-btn">Get In Touch With Us</div>
  <div class="abs dots"><span class="on"></span><span></span><span></span><span></span></div>
</section>

<section>
  <div class="abs about-panel">
    <h2 class="slab">About Ductless<br>Mini Splits</h2>
    <div class="rule"></div>
    <p class="about-lead">Excepteur sint occaecat cupidatat non proident sunt in culpa qui officia</p>
    <div class="about-copy">
      <p>Lorem ipsum dolor sit amet, consectetur adipiscing elit, sed do eiusmod tempor incididunt ut labore et dolore magna aliqua. Ut enim ad minim veniam, quis nostrud exercitation ullamco laboris nisi ut aliquip ex ea commodo consequat. Duis aute irure dolor in reprehenderit in voluptate velit esse cillum dolore eu fugiat nulla pariatur. Excepteur sint occaecat cupidatat non proident, sunt in culpa qui officia deserunt mollit anim id est laborum</p>
      <p>Sed ut perspiciatis unde omnis iste natus error sit voluptatem accusantium doloremque laudantium, totam rem aperiam, eaque ipsa quae ab illo inventore veritatis et quasi architecto beatae vitae dicta sunt explicabo. Nemo enim ipsam voluptatem quia voluptas sit aspernatur aut odit aut fugit, sed quia consequuntur magni dolores.</p>
    </div>
  </div>
  <div class="abs about-frame"></div>
  <div class="abs about-photo" role="img" aria-label="Wall-mounted mini split blowing cool air into a bright room"></div>
</section>

<section>
  <h2 class="abs slab help-title">How Can We Help You?</h2>
  <div class="abs help-rule"></div>

  <div class="abs svc-card" style="left:112px;top:1702px"><div class="svc-photo" role="img" aria-label="Hand opening the front panel of an indoor unit"></div><div class="svc-label">Ductless<br>Installation</div></div>
  <div class="abs svc-card" style="left:448px;top:1702px"><div class="svc-photo" role="img" aria-label="Remote pointed at an indoor unit blowing air"></div><div class="svc-label">Ductless for Additions &amp;<br>Remodels</div></div>
  <div class="abs svc-card" style="left:782px;top:1702px"><div class="svc-photo" role="img" aria-label="Technician working on a wall heating panel"></div><div class="svc-label">Baseboard Heat<br>Replacement</div></div>

  <div class="abs svc-card" style="left:112px;top:2003px"><div class="svc-photo" role="img" aria-label="Technician cleaning the filter of an indoor unit"></div><div class="svc-label">Ductless<br>Maintenance</div></div>
  <div class="abs svc-card" style="left:448px;top:2003px"><div class="svc-photo" role="img" aria-label="Screwdriver repairing the electronics of an open unit"></div><div class="svc-label">Ductless Repairs</div></div>
  <div class="abs svc-card" style="left:782px;top:2003px"><div class="svc-photo" role="img" aria-label="Close view of an outdoor heat pump fan grille"></div><div class="svc-label">Ductless Heat<br>Pump</div></div>

  <div class="abs btn more-btn">More Ductless Services</div>
</section>

<section>
  <div class="abs contact-bg" role="img" aria-label="Snow-covered house front in winter"></div>
  <h2 class="abs slab contact-title">Contact Us Today</h2>
  <div class="abs contact-rule"></div>
  <p class="abs contact-sub">Fill Out the Form Below</p>
  <div class="abs field" style="left:111px;top:2752px;width:205px">First Name</div>
  <div class="abs field" style="left:334px;top:2752px;width:203px">Last Name</div>
  <div class="abs field" style="left:111px;top:2812px;width:205px">Phone</div>
  <div class="abs field" style="left:334px;top:2812px;width:203px">Email</div>
  <div class="abs field" style="left:111px;top:2872px;width:426px">Are you a new customer?</div>
  <div class="abs field msg" style="left:111px;top:2932px;width:426px">Message</div>
  <div class="abs btn send-btn">Send Information</div>

  <div class="abs why-panel">
    <h2 class="slab">Why Choose<br>Copper Fern Services</h2>
    <div class="why-item" style="top:160px">
      <div class="why-icon" style="top:0"><svg width="28" height="28" viewBox="0 0 28 28" fill="none" stroke="#fff" stroke-width="2"><circle cx="14" cy="14" r="11"/><path d="M14 7v14M17.5 10.5c-1-1.2-5.5-1.6-6 .8-.6 3 6.6 2 6 5.4-.5 2.3-5 2-6.3.4"/></svg></div>
      <div class="why-text" style="top:-4px"><h3>0% Financing for 60 months</h3><p>Providing options to our customers where it matters most. Offer applies to Norvale systems.</p></div>
    </div>
    <div class="why-item" style="top:271px">
      <div class="why-icon" style="top:0"><svg width="28" height="28" viewBox="0 0 28 28" fill="none" stroke="#fff" stroke-width="2"><circle cx="14" cy="14" r="11"/><path d="M9 14.5l3.5 3.5L19 11"/></svg></div>
      <div class="why-text" style="top:-4px"><h3>365 Day, Money Back Guarantee</h3><p>We have integrity, and stand behind our services to ensure that you are satisfied.</p></div>
    </div>
    <div class="why-item" style="top:384px">
      <div class="why-icon" style="top:0"><svg width="28" height="28" viewBox="0 0 28 28" fill="none" stroke="#fff" stroke-width="2"><path d="M5 20h18M7 20v-4a7 7 0 0 1 14 0v4M14 9V6M11 20v-5M17 20v-5"/></svg></div>
      <div class="why-text" style="top:-15px"><h3>We Are the Experts in Ductless<br>Services</h3><p>Not only can we perform the services with precision, but we can also educate you on why ductless is the way to do.</p></div>
    </div>
  </div>
</section>

<footer>
  <div class="abs footer"></div>
  <div class="abs f-brand"><div class="brand-row"><span class="brand-dot"></span><span class="brand-name">Copper Fern Services</span></div></div>
  <div class="abs f-tag">DUCTLESS EXPERTS</div>
  <div class="abs slab f-head" style="left:112px;top:3470px">FOLLOW US</div>
  <div class="abs social" style="left:112px;top:3504px"><span></span><span></span><span></span></div>

  <div class="abs slab f-head" style="left:502px;top:3326px">LOCATION</div>
  <div class="abs f-line" style="left:502px;top:3373px">
    <svg width="12" height="16" viewBox="0 0 12 16" style="margin-top:7px"><path d="M6 0a6 6 0 0 0-6 6c0 4.5 6 10 6 10s6-5.5 6-10a6 6 0 0 0-6-6zm0 8.5A2.5 2.5 0 1 1 6 3.5a2.5 2.5 0 0 1 0 5z" fill="#fff"/></svg>
    <span>Copper Fern Services, Street Name,<br>City Name, Country code.</span>
  </div>
  <div class="abs f-line" style="left:500px;top:3449px">
    <svg width="15" height="15" viewBox="0 0 16 16" style="margin-top:7px"><path d="M3.6 1l2.3 2.8-1.4 1.9a9 9 0 0 0 5.8 5.8l1.9-1.4L15 12.4 13.4 15C6.8 15 1 9.2 1 2.6z" fill="#fff"/></svg>
    <span>Telephone: +01 555 014 2290</span>
  </div>
  <div class="abs f-line" style="left:500px;top:3501px">
    <svg width="15" height="12" viewBox="0 0 16 12" style="margin-top:9px"><rect width="16" height="12" rx="1" fill="#fff"/><path d="M1 1l7 6 7-6" stroke="#d8981b" stroke-width="1.5" fill="none"/></svg>
    <span>Email:hello@copperfernservices.com</span>
  </div>

  <div class="abs slab f-head" style="left:928px;top:3326px">QUICK LINKS</div>
  <nav class="f-links">
    <a style="top:3376px">Home</a>
    <a style="top:3406px">About Us</a>
    <a style="top:3436px">Financing</a>
    <a style="top:3466px">Contact Us</a>
    <a style="top:3495px">Privacy Policy</a>
    <a style="top:3525px">Site Map</a>
  </nav>

  <div class="abs f-rule"></div>
  <p class="abs copyright">Copyrights © 2019 Copper Fern Services. All rights reserved.</p>
</footer>

</body>
</html>
```